Doors for Chiropractic Office

In my chiropractic office I have 6 treatment rooms and 2 massage rooms. The entire office is going through a remodel. The overall color scheme is very earth tones but in order to add some color, the 6 doors to the treatment rooms will all be a separate color (Red, Blue, Yellow, Green etc)
I need to number each room 1,2,3,4,5,6 and the 2 massage rooms. I had the idea of putting a giant number on each door, so I am looking for some graphic ideas for that project.
The rooms are located with 4 on each side of a long hallway with the 2 massage rooms at the end.
The purpose of numbering each door is to direct the patients where to go.
I have uploaded pictures of the hall way. Pardon the dust since we are under construction but hopefully it gives you an idea of the layout. The door colors will change as stated above.

Requirements
Nice to have
• I would like to see someone come up with a design where each number for the doors are created out of vertebrae's.

```html
<!DOCTYPE html>
<html lang="en">
<head>
<meta charset="utf-8">
<title>Room Door Numbers</title>
<link rel="stylesheet" href="https://fonts.googleapis.com/css2?family=Playfair+Display:wght@500;700&family=Tinos:ital,wght@0,400;1,700&display=swap">
<style>
  :root {
    --wall: #dfd6cc;
    --red: #ed1c24;
    --red-soft: #ee5438;
    --red-number: #fde0d2;
    --blue: #3855a5;
    --blue-soft: #6d7fc0;
    --blue-number: #d2d8ee;
    --gold: #c5a72f;
    --gold-soft: #dcc35a;
    --gold-number: #f5f1df;
  }
  * { box-sizing: border-box; margin: 0; padding: 0; }
  html, body { width: 1200px; height: 1000px; overflow: hidden; }
  body { background: var(--wall); position: relative; }

  .door {
    position: absolute;
    top: 107px;
    width: 283px;
    height: 705px;
    overflow: hidden;
  }
  .door--four { left: 110px; background: var(--red); --soft: var(--red-soft); --number: var(--red-number); }
  .door--five { left: 474px; background: var(--blue); --soft: var(--blue-soft); --number: var(--blue-number); }
  .door--six  { left: 838px; background: var(--gold); --soft: var(--gold-soft); --number: var(--gold-number); }

  .door__ornament {
    position: absolute;
    inset: 0;
    background: radial-gradient(ellipse 90% 70% at 110% 55%, rgba(255,255,255,0.10), rgba(255,255,255,0) 70%);
  }

  .door__label {
    position: absolute;
    left: 8px;
    top: 194px;
    width: 130px;
    font-family: "Tinos", "Times New Roman", serif;
    color: var(--soft);
    transform: rotate(8deg);
    transform-origin: left top;
    line-height: 1;
  }
  .door__label-kind {
    display: block;
    font-size: 17px;
    letter-spacing: 0.5px;
  }
  .door__label-room {
    display: block;
    margin-left: 55px;
    margin-top: 6px;
    font-size: 20px;
    font-weight: 700;
    font-style: italic;
    letter-spacing: 1px;
  }

  .door__number {
    position: absolute;
    inset: 0;
    width: 283px;
    height: 705px;
  }
  .door__digit {
    font-family: "Playfair Display", "Times New Roman", serif;
    font-weight: 500;
    font-size: 312px;
    font-variant-numeric: lining-nums;
    font-feature-settings: "lnum" 1;
    fill: var(--number);
  }
</style>
</head>
<body>
  <section class="door door--four" aria-label="Treatment room 4">
    <div class="door__ornament" role="img" aria-label="Faint vertebrae spine ornament curving down the door"></div>
    <p class="door__label"><span class="door__label-kind">TREATMENT</span><span class="door__label-room">ROOM</span></p>
    <svg class="door__number" viewBox="0 0 283 705" aria-hidden="false">
      <text class="door__digit" x="112" y="606" text-anchor="middle">4</text>
    </svg>
  </section>

  <section class="door door--five" aria-label="Massage room 5">
    <div class="door__ornament" role="img" aria-label="Faint vertebrae spine ornament curving down the door"></div>
    <p class="door__label"><span class="door__label-kind">MASSAGE</span><span class="door__label-room">ROOM</span></p>
    <svg class="door__number" viewBox="0 0 283 705">
      <text class="door__digit" x="111" y="626" text-anchor="middle">5</text>
    </svg>
  </section>

  <section class="door door--six" aria-label="Massage room 6">
    <div class="door__ornament" role="img" aria-label="Faint vertebrae spine ornament curving down the door"></div>
    <p class="door__label"><span class="door__label-kind">MASSAGE</span><span class="door__label-room">ROOM</span></p>
    <svg class="door__number" viewBox="0 0 283 705">
      <text class="door__digit" x="115" y="622" text-anchor="middle">6</text>
    </svg>
  </section>
</body>
</html>
```